Growing the Ironclad Young Contender:
A Family Playbook for Nurturing Bold, Grounded, and Resilient Daughters at Games and Beyond.
📘 Book Cover Design Brief – “Growing the Ironclad Young Contender”

Project Title:
Design a bold, inspiring book cover for a best-selling book titled:
Growing the Ironclad Young Contender
Subtitle: A Family Playbook for Nurturing Bold, Grounded, and Resilient Daughters at Games and Beyond

🎯 Audience:

Parents of female athletes ages 14–20 who want their daughters to build confidence, strength, resilience, and long-term success both in sports and in life.

This book should feel encouraging, empowering, and credible — NOT cheesy, childish, or overly academic.

📕 Design Tone & Style:

Powerful and professional — should feel like a best-selling book from a leading performance or parenting expert

Emotionally compelling — conveys hope, resilience, strength, and possibility

Visually modern and clean — avoid anything overly busy, cliché, or childish

Heroic/aspirational tone — think transformation, leadership, strong positioning

💡 Visual Direction / Ideas (Use as Inspiration, Not Limitation):

Strong, confident teenage female athlete imagery — adaptable beyond one specific sport

Symbolic visuals — e.g. athlete standing strong, on a starting line, looking bold into the future, silhouette, or power stance

Bold typography that feels clean and modern (e.g., Proxima Nova, Montserrat, Gotham, Bebas Neue, etc.)

A title that stands out clearly when viewed as a thumbnail on Brindlemart

Color tones: Empowering, modern, and strong: think deep blues, greens, purples, or golds — avoid playful pastels or overly girly themes

Potential imagery: textured backgrounds, motion, bravery, development, strength, growth, sport/action overlays

🔥 What the Cover MUST Communicate:

✅ This is for parents who want strong, confident female athletes
✅ It’s a guidebook for personal development AND sports performance
✅ It’s about creating “IRONCLAD” confidence — physically, mentally and emotionally
✅ The message is: You can help your daughter become her strongest, most confident self

📚 Back-of-Book Summary (for context):

"Growing the Ironclad Young Contender" is a parent's blueprint to building girls who are strong in body, confident in mind, and ready to lead on and off the field. Through simple strategies around strength training, mindset, nutrition, and character development, this book gives parents the tools to help their daughters stay injury-resistant, break through mental barriers, and unlock their full potential — in sports and in life.

✅ Deliverables:

Full cover design (front, back, spine) for paperback
High-resolution files (print-ready)
Source files (PSD, AI, etc.)
3D mockup versions of the book (standing, flat, stack)

Target Market(s)

Industry/Entity Type

Fitness

Font styles to use
Sans Serif

Colors
FFF300
FFF600
FEFA6F
FFFEC7
FFFEE8

Requirements
Must have
• Bold Font
Should not have
• I don't want an image of a female athlete. I want this to be font based.

```html
<!DOCTYPE html>
<html lang="en">
<head>
<meta charset="utf-8">
<title>Growing the Ironclad Young Contender — Book Cover</title>
<link rel="stylesheet" href="https://fonts.googleapis.com/css2?family=Bebas+Neue&family=Montserrat:ital,wght@0,400;0,500;1,400&display=swap">
<style>
  :root {
    --cover-blue: #265a8e;
    --cover-blue-light: #2f67a2;
    --cover-blue-dark: #1d4874;
    --title-white: #ffffff;
    --title-gold: #c4a64c;
    --accent-gold: #e3c47c;
    --subtitle-white: #f4f4f4;
    --rule: rgba(190, 210, 235, 0.55);
  }
  * { margin: 0; padding: 0; box-sizing: border-box; }
  html, body {
    width: 840px;
    height: 1200px;
    overflow: hidden;
    background: #ffffff;
  }
  .book-cover {
    position: relative;
    width: 840px;
    height: 1200px;
    overflow: hidden;
    background:
      repeating-linear-gradient(0deg, rgba(255,255,255,0.025) 0 1px, transparent 1px 3px),
      radial-gradient(ellipse 70% 55% at 50% 42%, var(--cover-blue-light) 0%, var(--cover-blue) 55%, var(--cover-blue-dark) 100%);
  }
  .book-title {
    position: absolute;
    top: 56px;
    left: 0;
    width: 100%;
    text-align: center;
    font-family: "Bebas Neue", "Oswald", sans-serif;
    font-weight: 400;
    font-size: 168px;
    line-height: 145px;
    color: var(--title-white);
    text-transform: uppercase;
    letter-spacing: 0;
  }
  .book-title .title-line { display: block; }
  .book-title .title-highlight { color: var(--title-gold); }
  .divider {
    position: absolute;
    left: 110px;
    width: 620px;
    height: 2px;
    background: linear-gradient(90deg, transparent, var(--rule) 20%, var(--rule) 80%, transparent);
  }
  .divider-top { top: 846px; }
  .divider-bottom { top: 994px; }
  .book-subtitle {
    position: absolute;
    top: 866px;
    left: 80px;
    width: 680px;
    text-align: center;
    font-family: "Montserrat", sans-serif;
    font-weight: 400;
    font-size: 31px;
    line-height: 36px;
    color: var(--subtitle-white);
  }
  .book-subtitle em {
    font-style: italic;
    color: var(--accent-gold);
  }
  .author-name {
    position: absolute;
    top: 1060px;
    left: 0;
    width: 100%;
    text-align: center;
    font-family: "Montserrat", sans-serif;
    font-weight: 500;
    font-size: 52px;
    line-height: 60px;
    color: var(--subtitle-white);
    letter-spacing: 1px;
  }
</style>
</head>
<body>
  <main class="book-cover">
    <h1 class="book-title">
      <span class="title-line">Growing</span>
      <span class="title-line">The</span>
      <span class="title-line title-highlight">Ironclad</span>
      <span class="title-line">Young</span>
      <span class="title-line">Contender</span>
    </h1>
    <div class="divider divider-top"></div>
    <p class="book-subtitle">A Family Playbook for Nurturing <em>Bold, Grounded,</em> and <em>Resilient</em> Daughters at Games and Beyond</p>
    <div class="divider divider-bottom"></div>
    <p class="author-name">AUTHOR NAME</p>
  </main>
</body>
</html>
```